We need a new business card that reflects who we are. Professional, classy, modern, and service ori

We need a business card design for a window coverings design company in Kansas City called Bright Lane Interiors. We offer professional, modern, and high quality window covering products. We are looking to portray an image of a big, national franchise. We are a 5 location (with showrooms) business with 10 professional designers and 4 professional installers. These cards will be used with Thank you cards, given to realtors, and asked for referrals with.

Target Market(s)

Kansas City

Industry/Entity Type

Business

Contact Information for Business Card

We would like our card to look clean and simple on the front, featuring our logo and Marlow Fenwick's. Our designers' phone numbers and emails should be displayed as well as their title.

Font styles to use
Sans Serif

Colors

Designer to choose colors to be used in the design.

Requirements
Must have
• Front - Logos, name, phone number, email address
• Back - Showroom locations, social media? Appt date/time?
Nice to have
• I would like a clean and modern look (not contemporary. I like a white background, but I am open to ideas. Looking for a "National chain" look for a small business.
Should not have
• Too much busyness.

```html
<!DOCTYPE html>
<html lang="en">
<head>
<meta charset="utf-8">
<title>Bright Lane Interiors – Business Card</title>
<link rel="stylesheet" href="https://fonts.googleapis.com/css2?family=Roboto:wght@400;500;700&family=Roboto+Condensed:wght@400;700&display=swap">
<style>
  :root {
    --backdrop: #2b2b2b;
    --card: #f3f3f3;
    --brand-red: #c94046;
    --band-grey: #8e9196;
    --ink: #1e1e1e;
    --muted: #555a60;
    --dots: #8a8a8a;
    --partner-accent: #e8861f;
    --white: #ffffff;
  }
  * { box-sizing: border-box; margin: 0; padding: 0; }
  html, body { width: 1200px; height: 960px; overflow: hidden; }
  body {
    background: var(--backdrop);
    font-family: "Roboto", Arial, sans-serif;
    position: relative;
  }
  .card {
    position: absolute;
    width: 600px;
    height: 342px;
    background: var(--card);
  }
  .card--front { left: 322px; top: 108px; }
  .card--back { left: 320px; top: 493px; }

  /* Front */
  .brand {
    position: absolute;
    left: 0; right: 0; top: 92px;
    text-align: center;
  }
  .brand__row {
    display: inline-flex;
    align-items: center;
    gap: 12px;
  }
  .brand__square {
    width: 30px; height: 30px;
    background: var(--brand-red);
  }
  .brand__name {
    font-weight: 500;
    font-size: 34px;
    color: var(--ink);
    letter-spacing: 0.5px;
  }
  .brand__tagline {
    margin-top: 10px;
    font-family: "Roboto Condensed", Arial, sans-serif;
    font-size: 14px;
    color: var(--ink);
  }
  .contact-band {
    position: absolute;
    left: 0; right: 0; top: 253px;
    height: 61px;
    background: var(--band-grey);
  }
  .contact-band__panel {
    position: absolute;
    left: 50px; width: 500px; top: 0; bottom: 0;
    background: var(--brand-red);
    color: var(--white);
    text-align: center;
  }
  .contact-band__name {
    margin-top: 5px;
    font-family: "Roboto Condensed", Arial, sans-serif;
    font-weight: 700;
    font-size: 23px;
  }
  .contact-band__title {
    font-size: 17px;
    font-weight: 400;
  }
  .contact-band__details {
    margin-top: 1px;
    font-size: 15px;
  }

  /* Back */
  .partner {
    position: absolute;
    left: 0; right: 0; top: 41px;
    display: flex; justify-content: center; align-items: center; gap: 6px;
    font-family: "Roboto Condensed", Arial, sans-serif;
    font-weight: 700;
    font-size: 16px;
    color: var(--muted);
  }
  .partner__dot {
    width: 18px; height: 18px; border-radius: 50%;
    background: var(--partner-accent);
  }
  .appointments {
    position: absolute;
    left: 82px; top: 80px;
    list-style: none;
  }
  .appointments__row {
    display: flex; align-items: baseline;
    height: 45.5px;
    color: var(--brand-red);
  }
  .appointments__label { font-size: 17px; }
  .appointments__line {
    border-bottom: 1px dotted var(--dots);
    margin: 0 2px 0 4px;
  }
  .appointments__line--date { width: 170px; }
  .appointments__line--time { width: 106px; }
  .appointments__suffix { font-size: 13px; margin-left: 3px; }
  .showrooms {
    position: absolute;
    left: 0; right: 0; top: 259px;
    text-align: center;
  }
  .showrooms__heading {
    font-family: "Roboto Condensed", Arial, sans-serif;
    font-weight: 700;
    font-size: 15px;
    color: var(--brand-red);
  }
  .showrooms__list {
    margin-top: 4px;
    font-family: "Roboto Condensed", Arial, sans-serif;
    font-size: 13.5px;
    color: var(--muted);
  }
  .social {
    margin-top: 5px;
    display: flex; justify-content: center; gap: 3px;
  }
  .social__dot {
    width: 20px; height: 20px; border-radius: 50%;
    background: var(--brand-red);
  }
</style>
</head>
<body>
  <section class="card card--front">
    <div class="brand">
      <div class="brand__row">
        <span class="brand__square"></span>
        <span class="brand__name">Bright Lane Interiors</span>
      </div>
      <p class="brand__tagline">Custom Window Treatments, Drapery &amp; Home Style</p>
    </div>
    <div class="contact-band">
      <div class="contact-band__panel">
        <p class="contact-band__name">DANIEL REYES - <span class="contact-band__title">DESIGNER</span></p>
        <p class="contact-band__details">913.555.0148 | info@brightlaneinteriors.com | brightlaneinteriors.com</p>
      </div>
    </div>
  </section>

  <section class="card card--back">
    <div class="partner">
      <span>Marlow Fenwick Gallery</span>
      <span class="partner__dot"></span>
    </div>
    <ul class="appointments">
      <li class="appointments__row"><span class="appointments__label">Date :</span><span class="appointments__line appointments__line--date"></span><span class="appointments__label">Time :</span><span class="appointments__line appointments__line--time"></span><span class="appointments__suffix">AM/PM</span></li>
      <li class="appointments__row"><span class="appointments__label">Date :</span><span class="appointments__line appointments__line--date"></span><span class="appointments__label">Time :</span><span class="appointments__line appointments__line--time"></span><span class="appointments__suffix">AM/PM</span></li>
      <li class="appointments__row"><span class="appointments__label">Date :</span><span class="appointments__line appointments__line--date"></span><span class="appointments__label">Time :</span><span class="appointments__line appointments__line--time"></span><span class="appointments__suffix">AM/PM</span></li>
      <li class="appointments__row"><span class="appointments__label">Date :</span><span class="appointments__line appointments__line--date"></span><span class="appointments__label">Time :</span><span class="appointments__line appointments__line--time"></span><span class="appointments__suffix">AM/PM</span></li>
    </ul>
    <div class="showrooms">
      <p class="showrooms__heading">SHOWROOM LOCATIONS</p>
      <p class="showrooms__list">MAPLE RIDGE | CEDAR HOLLOW | BIRCH POINT | WESTBROOK | PINE VALE</p>
      <div class="social" aria-label="Social media links">
        <span class="social__dot"></span>
        <span class="social__dot"></span>
        <span class="social__dot"></span>
        <span class="social__dot"></span>
      </div>
    </div>
  </section>
</body>
</html>
```